Web design - holistic filmmaker

I need a design for my new website.

I am a holistic filmmaker, ie I make films for healers, alternative practitioners, spiritual people and institutions that offer training in this field.

The design should be noble, bright, convey the feeling of space and expanse and have some particularly beautiful color accents.

The structure is: start page, offer, references, about me, imprint.

As an idea for the start page, I thought that either I could introduce myself as a filmmaker and my offer, or we could start right on the start page with the references, ie photos and links to already realized projects.

If you want more information or an exchange, I'd love to hear from you. At the moment I just don't know how to describe it better.

The winner will then be asked to design a logo.

Target Market(s)

healers, alternative practitioners, spiritual people and institutions that offer training in this field

Industry/Entity Type

Film production

Number of Pages Required

3 page

```html
<!DOCTYPE html>
<html lang="en">
<head>
<meta charset="utf-8">
<title>Arlo Venner — Holistic Filmmaker</title>
<link href="https://fonts.googleapis.com/css2?family=Anton&family=Montserrat:wght@300;400;500;600;700&display=swap" rel="stylesheet">
<style>
:root{
  --ink:#3a3a3a;
  --ink-dark:#2b2b2b;
  --band:#d6d6d6;
  --page:#f2f2f2;
  --white:#ffffff;
  --footer:#121212;
  --footer-bar:#0b0b0b;
  --muted:#6c6c6c;
  --outline:#9a9a9a;
}
*{box-sizing:border-box;margin:0;padding:0}
html,body{width:1200px;height:5196px;overflow:hidden}
body{background:var(--page);font-family:'Montserrat',sans-serif;color:var(--ink);position:relative}
.abs{position:absolute}
.media{position:absolute}

/* header */
.logo{left:137px;top:38px;font-size:30px;font-weight:400;letter-spacing:1px;color:var(--ink-dark);z-index:3}
.nav{left:424px;top:50px;display:flex;gap:50px;font-size:10.5px;letter-spacing:.5px;color:var(--ink);z-index:3}
.nav .active{font-weight:700;position:relative}
.nav .active::before{content:"";position:absolute;left:0;right:0;top:-38px;height:2px;background:var(--ink-dark)}
.contact-btn{left:948px;top:40px;width:119px;height:31px;background:var(--ink-dark);color:var(--white);font-size:9px;font-weight:700;letter-spacing:2px;display:flex;align-items:center;justify-content:center;gap:8px;z-index:3}
.header-rule{left:125px;top:97px;width:950px;height:1px;background:#9c9c9c;z-index:3}

/* hero */
.hero{left:12px;top:0;width:1176px;height:762px;background:linear-gradient(180deg,#e6e6e6 0%,#bdbdbd 55%,#5a5a5a 78%,#2e2e2e 100%)}
.hero-kicker{left:0;width:1200px;top:170px;text-align:center;font-size:36px;font-weight:400;letter-spacing:1px;color:var(--ink-dark)}
.hero-word{left:0;width:1200px;top:195px;text-align:center;font-family:'Anton',sans-serif;font-size:270px;line-height:1;color:var(--white);text-shadow:8px 6px 0 var(--ink-dark)}

/* about */
.about-band{left:12px;top:778px;width:1176px;height:418px;background:var(--band)}
.about-title{left:198px;top:880px;font-size:42px;line-height:52px;font-weight:400;color:var(--ink-dark)}
.about-rule{left:540px;top:848px;width:2px;height:217px;background:var(--ink-dark)}
.about-text{left:575px;top:843px;width:430px;font-size:10.5px;line-height:19.5px;color:var(--ink)}
.about-text p+p{margin-top:20px}
.outline-word{font-family:'Anton',sans-serif;line-height:1;color:transparent;-webkit-text-stroke:1.5px var(--outline);letter-spacing:2px}
.about-outline{left:0;width:1200px;text-align:center;top:1118px;font-size:158px}

/* work rows */
.work-copy{width:578px;text-align:center}
.work-num{font-family:'Anton',sans-serif;font-size:96px;line-height:1;color:var(--ink-dark);text-shadow:4px 3px 0 #b0b0b0}
.work-line{margin-top:18px;font-size:38px;line-height:45px;font-weight:400;color:var(--ink-dark)}

/* film band */
.film{left:12px;top:2985px;width:1176px;height:702px;background:linear-gradient(90deg,#6b5a45 0%,#8a7a5e 30%,#3e4a2e 60%,#25301e 100%)}
.film-kicker{left:500px;width:493px;top:3238px;text-align:right;font-size:34px;line-height:40px;color:var(--white)}
.film-word{left:400px;width:593px;top:3305px;text-align:right;font-family:'Anton',sans-serif;font-size:300px;line-height:1;color:var(--white);text-shadow:8px 6px 0 var(--ink-dark)}

/* offers */
.offers-band{left:12px;top:3701px;width:1176px;height:611px;background:var(--band)}
.offers-title{left:198px;top:3880px;font-size:44px;line-height:53px;color:var(--ink-dark)}
.offers-text{left:198px;top:4048px;width:240px;font-size:10px;line-height:19px;color:var(--ink)}
.card{text-align:center}
.card-premium{left:601px;top:3786px;width:278px;height:417px;background:var(--ink-dark);color:var(--white)}
.card-pro{left:894px;top:3844px;width:197px;height:299px;background:var(--white);color:var(--ink-dark);box-shadow:0 2px 10px rgba(0,0,0,.08)}
.card h3{font-weight:700}
.card .price{font-family:'Anton',sans-serif}
.card .price small{font-family:'Montserrat',sans-serif;font-size:.3em;font-weight:400}
.card .btn{display:block;margin:0 auto;font-weight:700}
.card-premium h3{font-size:18px;margin-top:34px}
.card-premium .sub{font-size:12px;margin-top:10px;color:#d0d0d0}
.card-premium .price{font-size:44px;margin-top:26px}
.card-premium .rule{height:1px;background:#5a5a5a;margin:22px 0 26px}
.card-premium li{list-style:none;font-size:13px;line-height:36px;color:#e0e0e0}
.card-premium .btn{width:176px;height:44px;line-height:44px;background:var(--white);color:var(--ink-dark);font-size:12px;margin-top:24px}
.card-pro h3{font-size:12px;margin-top:26px}
.card-pro .sub{font-size:8px;margin-top:6px;color:var(--muted)}
.card-pro .price{font-size:30px;margin-top:18px}
.card-pro .rule{height:1px;background:#e2e2e2;margin:14px 0 16px}
.card-pro li{list-style:none;font-size:9px;line-height:26px;color:var(--muted)}
.card-pro .btn{width:124px;height:32px;line-height:32px;background:var(--ink-dark);color:var(--white);font-size:9px;margin-top:14px}
.offers-outline{left:121px;top:4206px;font-size:150px}

/* newsletter */
.email-field{left:198px;top:4480px;width:411px;height:50px;background:var(--white);font-size:10px;letter-spacing:1px;color:var(--muted);padding:19px 0 0 44px}
.subscribe{left:198px;top:4548px;width:264px;height:45px;background:var(--ink-dark);color:var(--white);font-size:11px;font-weight:700;letter-spacing:4px;display:flex;align-items:center;justify-content:center}
.stay{left:692px;top:4425px;font-family:'Anton',sans-serif;font-size:170px;line-height:1;color:var(--ink-dark);text-shadow:6px 4px 0 #b0b0b0}
.know{left:692px;top:4602px;font-size:34px;color:var(--ink-dark);letter-spacing:1px}

/* footer */
.footer{left:12px;top:4776px;width:1176px;height:404px;background:var(--footer)}
.footer-outline{left:0;width:1200px;text-align:center;top:4700px;font-size:178px;-webkit-text-stroke:1.5px #8a8a8a}
.footer-nav{left:0;width:1200px;top:4950px;display:flex;justify-content:center;gap:38px;font-size:11px;color:#e6e6e6;letter-spacing:.5px}
.contact-item{display:flex;align-items:center;gap:13px;color:#e6e6e6}
.contact-item .dot{width:34px;height:34px;border-radius:50%;background:#4a4a4a;display:flex;align-items:center;justify-content:center}
.contact-item .label{font-size:7px;font-weight:700;letter-spacing:2px}
.contact-item .value{font-size:11px;margin-top:3px;line-height:17px}
.contact-item .value.small{font-size:9px}
.footer-bar{left:12px;top:5140px;width:1176px;height:40px;background:var(--footer-bar);border-top:1px solid #2a2a2a}
.copyright{left:198px;top:5154px;font-size:8px;color:#cfcfcf;letter-spacing:.5px}
.social{top:5153px;width:14px;height:14px;border-radius:50%;background:#3a3a3a}
</style>
</head>
<body>

<!-- hero -->
<div class="media hero" role="img" aria-label="Black and white photo of a film crew with a camera on a tripod silhouetted against a misty landscape"></div>
<div class="abs logo">ARLO VENNER</div>
<nav class="abs nav">
  <span class="active">HOME</span><span>OFFER</span><span>REFRENCES</span><span>ABOUT ME</span><span>IMPRINT</span>
</nav>
<div class="abs contact-btn">CONTACT
  <svg width="18" height="8" viewBox="0 0 18 8"><path d="M0 4h16M13 1l3 3-3 3" stroke="#fff" fill="none" stroke-width="1"/></svg>
</div>
<div class="abs header-rule"></div>
<div class="abs hero-kicker">MOVIES FOR AWAKENED</div>
<div class="abs hero-word">ONES</div>

<!-- about -->
<section class="abs about-band"></section>
<h2 class="abs about-title">I AM A<br>HOLISTIC<br>FILMMAKER.</h2>
<div class="abs about-rule"></div>
<div class="abs about-text">
  <p>My name is Arlo and I do movies - with enthusiasm and wholeheartedly. I am a holistic filmmaker. At the end of the 1990s, I was faced with the question of whether I should go into alternative medicine or the film industry as a career. Professionally, I chose film at that time, but the spiritual and my passion for the so-called alternative healing methods have accompanied me almost as intensely ever since.</p>
  <p>My cinematic path literally brought me from cable guy to cameraman, director and producer. It all started in 1995 as a camera assistant for the US news agency. In the following years, I worked in various positions on numerous national and international television productions, cinema and documentary films, commercials and live productions.</p>
</div>
<div class="abs outline-word about-outline">ABOUT ME</div>

<!-- work rows -->
<div class="media" style="left:12px;top:1333px;width:579px;height:410px;background:linear-gradient(135deg,#b89a86,#c24a7a 55%,#8a6a5a)" role="img" aria-label="Video still of a woman in a pink sweater standing before a flip chart"></div>
<div class="abs work-copy" style="left:611px;top:1412px"><div class="work-num">01</div><div class="work-line">LOREM IPSUM IS<br>SIMPLY DUMMY TEXT<br>OF THE PRINTING</div></div>

<div class="media" style="left:610px;top:1743px;width:578px;height:409px;background:linear-gradient(135deg,#4a4a4a,#9a9a9a 50%,#3a3a3a)" role="img" aria-label="Black and white video still of a couple tending to a resting person"></div>
<div class="abs work-copy" style="left:12px;top:1822px"><div class="work-num">02</div><div class="work-line">LOREM IPSUM IS<br>SIMPLY DUMMY TEXT<br>OF THE PRINTING</div></div>

<div class="media" style="left:12px;top:2152px;width:579px;height:410px;background:linear-gradient(160deg,#dcdcdc,#a8a8a8 50%,#3c3c3c)" role="img" aria-label="Black and white video still of a woman in front of a television tower"></div>
<div class="abs work-copy" style="left:611px;top:2231px"><div class="work-num">03</div><div class="work-line">LOREM IPSUM IS<br>SIMPLY DUMMY TEXT<br>OF THE PRINTING</div></div>

<div class="media" style="left:610px;top:2562px;width:578px;height:409px;background:linear-gradient(135deg,#6a6a6a,#3a3a3a 50%,#8a8a8a)" role="img" aria-label="Black and white video still of a singer performing outdoors by a music stand"></div>
<div class="abs work-copy" style="left:12px;top:2641px"><div class="work-num">04</div><div class="work-line">LOREM IPSUM IS<br>SIMPLY DUMMY TEXT<br>OF THE PRINTING</div></div>

<!-- film band -->
<div class="media film" role="img" aria-label="Portrait photo of the filmmaker in an orange shirt against a green background"></div>
<div class="abs film-kicker">THE PRODUCTION<br>OF YOUR</div>
<div class="abs film-word">FILM</div>

<!-- offers -->
<section class="abs offers-band"></section>
<h2 class="abs offers-title">AS A FULL-<br>SERVICE<br>PROVIDER</h2>
<p class="abs offers-text">I offer everything from one source, from consulting and conception to the finished film.</p>

<div class="abs card card-premium">
  <h3>Premium Package</h3>
  <div class="sub">2 Hour Session</div>
  <div class="price">$49<small>/Month</small></div>
  <div class="rule"></div>
  <ul><li>20 Digital Images</li><li>Online Gallery</li><li>2 Photographer</li></ul>
  <span class="btn">Try for Free</span>
</div>
<div class="abs card card-pro">
  <h3>Professional Package</h3>
  <div class="sub">3 Hour Session</div>
  <div class="price">$199<small>/Month</small></div>
  <div class="rule"></div>
  <ul><li>30 Digital Images</li><li>30 Digital Images</li><li>4 Photographer</li></ul>
  <span class="btn">Try for Free</span>
</div>
<div class="abs outline-word offers-outline">OFFERS</div>

<!-- newsletter -->
<div class="abs email-field">EMAIL</div>
<div class="abs subscribe">SUBSCRIBE NOW</div>
<div class="abs stay">STAY</div>
<div class="abs know">IN THE KNOW!</div>

<!-- footer -->
<footer class="abs footer"></footer>
<div class="abs outline-word footer-outline">ARLO VENNER</div>
<nav class="abs footer-nav">
  <span>HOME</span><span>OFFER</span><span>REFRENCES</span><span>ABOUT ME</span><span>IMPRINT</span><span>CONTACT</span>
</nav>

<div class="abs contact-item" style="left:304px;top:5015px">
  <span class="dot"><svg width="14" height="10" viewBox="0 0 14 10"><rect x=".5" y=".5" width="13" height="9" fill="none" stroke="#ddd"/><path d="M.5 .5L7 6l6.5-5.5" fill="none" stroke="#ddd"/></svg></span>
  <div><div class="label">EMAIL:</div><div class="value">hello@arlovenner.com</div></div>
</div>
<div class="abs contact-item" style="left:529px;top:5015px">
  <span class="dot"><svg width="14" height="14" viewBox="0 0 24 24"><path fill="#ddd" d="M6.6 10.8a15 15 0 006.6 6.6l2.2-2.2c.3-.3.7-.4 1-.2 1.1.4 2.3.6 3.6.6.6 0 1 .4 1 1V20c0 .6-.4 1-1 1A17 17 0 013 4c0-.6.4-1 1-1h3.5c.6 0 1 .4 1 1 0 1.3.2 2.5.6 3.6.1.3 0 .7-.2 1z"/></svg></span>
  <div><div class="label">PHONE:</div><div class="value">0000-999-888</div></div>
</div>
<div class="abs contact-item" style="left:751px;top:5008px">
  <span class="dot"><svg width="12" height="16" viewBox="0 0 12 16"><path fill="#ddd" d="M6 0a6 6 0 00-6 6c0 4.5 6 10 6 10s6-5.5 6-10a6 6 0 00-6-6zm0 8.5A2.5 2.5 0 116 3.5a2.5 2.5 0 010 5z"/></svg></span>
  <div><div class="label">ADDRESS:</div><div class="value small">Lorem Ipsum is simply<br>dummy text of the printing</div></div>
</div>

<div class="abs footer-bar"></div>
<div class="abs copyright">COPYRIGHT © 2023 ARLO VENNER. ALL RIGHT RESERVED</div>
<span class="abs social" style="left:891px"></span>
<span class="abs social" style="left:937px"></span>
<span class="abs social" style="left:983px"></span>

</body>
</html>
```